The Harbourlight Dental centre, the Zorvik of dentistry

New concept of running a dental practice by having a walk in practice
WE ARE A HUSBAND AND WIFE TEAM

Really modern and sophisticated, we want it to feel different from the traditional dental practice.
we want it split into different pages:CONTACT US
LOCATION: Information about our location since patients often confuse us with the practice across the road
ABOUT US:
Opening hours - & 7 Days, We offer a weekend service
WALK IN: We offer a walk in service for dental treatments
TREATMENTS we offer

DENTAL ADVICE: Free dentist advise call back- So a dentist will call you back for free to discuss

Target Market(s)

Everyone

Industry/Entity Type

Dental

Coding

Coded - Design and coding required

Number of Pages Required

5+ page

Requirements
Must have
• First page
• * changing pictures
• *opening times
• * our walk in concept I.e. no appointment needed
• *logo
• * links in to clinic tidal (online booking system in Australia)
• * address /phone number/email
• * possible videos
• Second page
• meet the team
• third page
• dental treatments/walk in treatments
• fourth page
• dental advice with vid larko videos
• Fifth page
• contact us/maps/ we get confused with the dental practice across the road
• We would also like a giving back page. In this please include the photo's below of our dental mission in Guatemala, where by we did treatment for patients as part of a charity.
Nice to have
• Changing pictures on the home screen
• videos linked to home page

```html
<!DOCTYPE html>
<html lang="en">
<head>
<meta charset="utf-8">
<title>The Harbourlight Dental centre</title>
<link href="https://fonts.googleapis.com/css2?family=Open+Sans:ital,wght@0,400;0,600;0,700;1,600;1,700;1,800&display=swap" rel="stylesheet">
<style>
:root{
  --blue:#1ea7e1;
  --blue-dark:#178fc4;
  --green:#8cc63f;
  --green-dark:#76ad2c;
  --ink:#4a4a4a;
  --muted:#8a8a8a;
  --line:#e4e4e4;
  --white:#ffffff;
  --paper:#f6f6f6;
}
*{box-sizing:border-box;margin:0;padding:0}
html,body{width:1200px;height:2816px;overflow:hidden}
body{font-family:"Open Sans",Arial,sans-serif;color:var(--ink);background:var(--white);position:relative}
.abs{position:absolute}

/* top bar */
.topbar{left:0;top:0;width:1200px;height:34px;background:var(--blue);color:var(--white);font-size:13px;display:flex;justify-content:space-between;align-items:center;padding:0 60px}
.topbar span{display:flex;align-items:center;gap:8px}
.topbar b{font-weight:700}

/* header */
.header{left:0;top:34px;width:1200px;height:110px;display:flex;align-items:center;justify-content:space-between;padding:0 60px;border-bottom:1px solid var(--line)}
.brand{display:flex;align-items:center;gap:12px}
.brand-dot{width:40px;height:40px;border-radius:50%;background:var(--green)}
.brand-name{font-size:20px;font-weight:700;color:var(--blue);line-height:1.1;width:190px}
.nav{display:flex;gap:0;font-size:14px}
.nav a{color:var(--ink);text-decoration:none;padding:10px 20px;border-left:1px solid var(--line)}
.nav a:first-child{border-left:none}

/* hero */
.hero{left:0;top:145px;width:1200px;height:465px;background:linear-gradient(120deg,#c9d98f 0%,#e9d3bf 40%,#9bbf5a 75%,#6f9c3a 100%)}
.hero-copy{left:300px;top:310px;width:600px;text-align:center;color:var(--white);font-size:19px;line-height:1.45;text-shadow:0 1px 3px rgba(0,0,0,.35)}
.hero-btn{left:465px;top:420px;width:270px;height:50px;background:var(--white);color:var(--blue);font-weight:700;font-size:14px;border-radius:4px;display:flex;align-items:center;justify-content:center;letter-spacing:.3px}
.dots{left:560px;top:545px;display:flex;gap:10px}
.dots i{width:10px;height:10px;border-radius:50%;background:rgba(255,255,255,.6)}
.dots i.on{background:var(--white)}

/* treatments */
.section-title{font-style:italic;font-weight:800;font-size:44px;letter-spacing:.5px}
.t-title{left:0;top:650px;width:1200px;text-align:center;color:var(--green)}
.t-sub{left:0;top:712px;width:1200px;text-align:center;color:var(--muted);font-size:14px}
.card{top:770px;width:290px}
.card-photo{width:290px;height:180px;background:linear-gradient(135deg,#b9c2c8,#7f8d96)}
.card-head{display:flex;align-items:center;gap:10px;margin-top:14px;font-size:18px;font-weight:600;color:var(--ink);border-bottom:3px solid var(--blue);padding-bottom:10px;white-space:nowrap}
.card-head .tick{width:22px;height:22px;flex:none}
.card-text{margin-top:10px;font-size:12px;color:var(--muted);line-height:1.6;width:290px}

/* team */
.team-band{left:0;top:1130px;width:1200px;height:560px}
.team-title{left:140px;top:1210px;color:var(--white)}
.team-text{left:140px;top:1280px;width:440px;color:var(--white);font-size:17px;line-height:1.5}
.hex{clip-path:polygon(25% 3%,75% 3%,100% 50%,75% 97%,25% 97%,0 50%)}
.hex-frame{background:var(--white)}
.hex-photo{background:linear-gradient(160deg,#9bb3c4,#3c6a8a)}
.role{font-size:14px;color:var(--ink)}
.person{font-size:34px;font-style:italic;font-weight:700;color:var(--blue)}

/* about */
.about-title{left:140px;top:1720px;color:var(--blue)}
.about-text{left:140px;top:1790px;width:460px;font-size:14px;line-height:1.65;color:var(--ink)}
.learn{left:140px;top:1935px;width:150px;height:44px;background:var(--green);color:var(--white);font-size:14px;font-weight:600;display:flex;align-items:center;justify-content:center;border-radius:3px}
.about-photo{left:615px;top:1705px;width:440px;height:280px;background:linear-gradient(135deg,#a8b9c8,#6f8aa3);border:6px solid var(--white);box-shadow:0 2px 8px rgba(0,0,0,.2)}

/* advice */
.advice{left:0;top:2025px;width:1200px;height:140px;background:var(--blue);display:flex;align-items:center;padding-left:140px;gap:30px}
.advice h2{font-style:italic;font-weight:800;font-size:36px;color:var(--white);white-space:nowrap}
.advice .bar{width:2px;height:60px;background:rgba(255,255,255,.7)}
.advice p{font-style:italic;font-size:19px;color:var(--white);width:600px;line-height:1.4}

/* contact */
.contact{left:0;top:2165px;width:1200px;height:515px;background:linear-gradient(180deg,#8b8f93,#5f6468)}
.contact-title{left:0;top:2195px;width:1200px;text-align:center;color:var(--white)}
.map{left:140px;top:2300px;width:580px;height:330px;background:#e6e3dc}
.address{left:720px;top:2300px;width:340px;height:330px;background:var(--green);color:var(--white);padding:36px 30px}
.address h3{font-style:italic;font-weight:800;font-size:26px;margin-bottom:22px}
.address p{font-size:17px;line-height:1.5}
.address .phone{font-size:38px;font-weight:700;margin-top:36px;letter-spacing:.5px}

/* footer */
.footer{left:0;top:2680px;width:1200px;height:136px;border-top:4px solid var(--blue);display:flex;align-items:center;justify-content:space-between;padding:0 140px}
.footer .brand-name{font-size:16px;width:150px}
.footer .brand-dot{width:30px;height:30px}
.foot-mid{text-align:center}
.foot-links{display:flex;gap:16px;font-size:12px;color:var(--ink)}
.foot-copy{margin-top:10px;font-size:11px;color:var(--muted)}
.partner{display:flex;align-items:center;gap:8px;font-size:16px;font-weight:700;color:var(--green-dark)}
.partner i{width:14px;height:14px;background:var(--green-dark)}
</style>
</head>
<body>

<div class="abs topbar">
  <span><svg width="14" height="14" viewBox="0 0 24 24"><path fill="#fff" d="M6.6 10.8a15 15 0 0 0 6.6 6.6l2.2-2.2c.3-.3.7-.4 1-.2 1.1.4 2.300.6 3.6.6.6 0 1 .4 1 1V20c0 .6-.4 1-1 1A17 17 0 0 1 3 4c0-.6.4-1 1-1h3.5c.6 0 1 .4 1 1 0 1.3.2 2.5.6 3.6.1.3 0 .7-.2 1z"/></svg><b>Phone Number:</b> (08) 5120 4417</span>
  <span><svg width="14" height="14" viewBox="0 0 24 24"><circle cx="12" cy="12" r="9" fill="none" stroke="#fff" stroke-width="2"/><path d="M12 7v5l3 2" stroke="#fff" stroke-width="2" fill="none"/></svg><b>Opening Times:</b> OPEN 8 AM TO 8PM 7 DAYS A WEEK</span>
</div>

<header class="abs header">
  <div class="brand"><div class="brand-dot"></div><div class="brand-name">The Harbourlight Dental centre</div></div>
  <nav class="nav"><a>Home</a><a>About Us</a><a>Meet the Team</a><a>Dental Treatments</a><a>Dental Advice</a><a>Contact Us</a></nav>
</header>

<div class="abs hero" role="img" aria-label="Photo of a smiling child outdoors on green grass"></div>
<p class="abs hero-copy">Walk in any day of the week for friendly care,<br>no booking needed, we are ready for you.</p>
<div class="abs hero-btn">NO NEED OF APPOINTMENT</div>
<div class="abs dots"><i class="on"></i><i></i><i></i><i></i></div>

<h2 class="abs section-title t-title">WALK IN TREATMENTS</h2>
<p class="abs t-sub">We offer a walk in service for dental treatments</p>

<div class="abs card" style="left:140px">
  <div class="card-photo" role="img" aria-label="Photo of the clinic building and car park"></div>
  <div class="card-head"><svg class="tick" viewBox="0 0 24 24"><circle cx="12" cy="12" r="11" fill="#8cc63f"/><path d="M7 12.5l3.2 3.2L17 9" stroke="#fff" stroke-width="2.4" fill="none"/></svg>Walk In Exam</div>
  <p class="card-text">Drop in at any time for a full check of your teeth and gums. Our dentists explain what they find and plan the next steps with you on the spot.</p>
</div>
<div class="abs card" style="left:455px">
  <div class="card-photo" role="img" aria-label="Photo of a dentist treating a patient"></div>
  <div class="card-head"><svg class="tick" viewBox="0 0 24 24"><circle cx="12" cy="12" r="11" fill="#8cc63f"/><path d="M7 12.5l3.2 3.2L17 9" stroke="#fff" stroke-width="2.4" fill="none"/></svg>Walk In Scale &amp; Polish</div>
  <p class="card-text">A gentle clean that lifts plaque and stains, leaving a fresh smile. Come in on your way to work or at the weekend, with no wait for a slot.</p>
</div>
<div class="abs card" style="left:770px">
  <div class="card-photo" role="img" aria-label="Photo of a filling treatment in the surgery"></div>
  <div class="card-head"><svg class="tick" viewBox="0 0 24 24"><circle cx="12" cy="12" r="11" fill="#8cc63f"/><path d="M7 12.5l3.2 3.2L17 9" stroke="#fff" stroke-width="2.4" fill="none"/></svg>Walk In Filling</div>
  <p class="card-text">Tooth-coloured fillings placed the same day you walk in. Quick, comfortable repair for chips and small holes so you can get back to your day.</p>
</div>

<svg class="abs team-band" viewBox="0 0 1200 560" aria-hidden="true">
  <polygon points="0,60 1200,0 1200,500 0,560" fill="#1ea7e1"/>
  <polygon points="560,140 1200,30 1200,330 640,420" fill="#ffffff"/>
  <polygon points="80,330 640,250 600,520 80,560" fill="#ffffff"/>
</svg>
<h2 class="abs section-title team-title">MEET THE TEAM</h2>
<p class="abs team-text">We want our patients to feel safe, happy and have dental treatment which is accessible.</p>

<div class="abs hex hex-frame" style="left:620px;top:1225px;width:260px;height:230px"></div>
<div class="abs hex hex-photo" style="left:632px;top:1236px;width:236px;height:208px" role="img" aria-label="Portrait photo of dentist Rajan"></div>
<div class="abs role" style="left:905px;top:1365px">Dentist</div>
<div class="abs person" style="left:905px;top:1385px">Rajan</div>

<div class="abs hex hex-frame" style="left:190px;top:1420px;width:230px;height:204px"></div>
<div class="abs hex hex-photo" style="left:201px;top:1430px;width:208px;height:184px" role="img" aria-label="Portrait photo of dentist Elise"></div>
<div class="abs role" style="left:440px;top:1560px">Dentist</div>
<div class="abs person" style="left:440px;top:1580px">Elise</div>

<h2 class="abs section-title about-title">ABOUT US</h2>
<p class="abs about-text">Welcome to The Harbourlight Dental centre – your general and cosmetic dentist in the heart of Larkhaven. Whether it's cosmetic hygiene treatment, tooth whitening, or botox facial rejuvenation, located within the busy medical centre with free parking all around.</p>
<div class="abs learn">Learn More</div>
<div class="abs about-photo" role="img" aria-label="Group photo of the dental team outside the clinic"></div>

<section class="abs advice">
  <h2>DENTAL ADVISE</h2>
  <div class="bar"></div>
  <p>Free dentist advise call back- So a dentist will call you back for free to discuss</p>
</section>

<div class="abs contact" role="img" aria-label="Faded photo of the street outside the clinic"></div>
<h2 class="abs section-title contact-title">CONTACT US</h2>
<div class="abs map" role="img" aria-label="Street map showing the clinic location"></div>
<div class="abs address">
  <h3>OUR ADDRESS</h3>
  <p>Unit 7, 18 Corvella Parade,<br>Larkhaven,<br>WA 6190.</p>
  <div class="phone">08 5120 4417</div>
</div>

<footer class="abs footer">
  <div class="brand"><div class="brand-dot"></div><div class="brand-name">The Harbourlight Dental centre</div></div>
  <div class="foot-mid">
    <div class="foot-links"><span>Home</span><span>About Us</span><span>Meet the Team</span><span>Dental Treatments</span><span>Dental Advice</span><span>Contact Us</span></div>
    <div class="foot-copy">© 2024 Harbourlight Dental. All Rights Reserved.</div>
  </div>
  <div class="partner"><i></i>clinic tidal</div>
</footer>

</body>
</html>
```